Celvara Health Group Presentation Folder, for Cancer Awareness, VERY COLORFUL AND MODERN

Presentation Folder I know pretty much what i want so it should be very eazy , I have included files from folders I use now rebrand them to my new company they will be fine, no sense re creating the wheel
Full Bleed Size
20.87" x 16.68"
53 x 42.4 cm
6260 x 5004 pixels
Document Trim Size
20.75" x 16.56"
52.7 x 42.1 cm
6225 x 4969 pixels

Low design quality

Industry/Entity Type

Medical

Font styles to use
Serif

Colors

Designer to choose colors to be used in the design.

Requirements
Must have
• really I am not looking for some one to redesign, we like our folder front page and would like to see new word information added., there are two folder front pages to choose from
• So Keep the original front page and redesign the back page and the pockets
• Can Make your Design off of one of the ones I already uploaded
Nice to have
• Keep the same color schemes, Keep the original front page and redesign the back page and the pockets
Should not have
• DO not recreate the front covers, use what I gave you and just rebrand

```html
<!DOCTYPE html>
<html lang="en">
<head>
<meta charset="utf-8">
<title>Celvara Health Group – Hereditary Cancer Screening Folder</title>
<link rel="stylesheet" href="https://fonts.googleapis.com/css2?family=Raleway:wght@400;600;700;800&family=Open+Sans:wght@400;600;700&display=swap">
<style>
  :root{
    --bg:#e6e6e8;
    --paper:#ffffff;
    --pink:#d26db0;
    --pink-soft:#d592c2;
    --blue:#6478ad;
    --blue-deep:#5f72a8;
    --navy:#1f2d5a;
    --heading-blue:#4a5f9f;
    --sky:#3ab0e2;
    --text:#3c3c46;
  }
  *{margin:0;padding:0;box-sizing:border-box}
  html,body{width:902px;height:1200px;overflow:hidden;background:var(--bg)}
  .folder{position:absolute;left:22px;top:227px;width:817px;height:710px;transform:scale(1.05);transform-origin:0 0}
  .spread{position:absolute;left:0;top:0;width:817px;height:515px;background:var(--paper)}
  .hero-art{position:absolute;left:60px;top:15px;width:285px;height:285px}
  .intro{position:absolute;left:40px;top:325px;width:345px;font:400 10px/1.3 'Open Sans',sans-serif;color:var(--text);text-align:justify}
  .intro strong{color:var(--pink);font-weight:700}
  .motto{position:absolute;left:20px;top:415px;width:370px;text-align:center;font:700 14.5px/1.35 'Raleway',sans-serif;color:var(--heading-blue)}
  .title{position:absolute;left:423px;top:53px;font:800 22px/1 'Raleway',sans-serif;color:var(--pink);letter-spacing:.2px}
  .subtitle{position:absolute;left:430px;top:87px;font:400 17px/1 'Raleway',sans-serif;color:var(--navy)}
  .lead{position:absolute;left:420px;top:112px;width:390px;text-align:center;font:400 13px/1.25 'Raleway',sans-serif;color:var(--navy)}
  .photo-frame{position:absolute;left:440px;top:160px;width:375px;height:240px}
  .band{position:absolute;left:408px;top:428px;width:409px;height:39px;background:var(--blue)}
  .band-text{position:absolute;left:108px;top:12px;font:700 13px/1 'Open Sans',sans-serif;color:#fff;letter-spacing:.2px}
  .brand-seal{position:absolute;left:32px;top:-8px;width:58px;height:58px;border-radius:50%;background:#fff;display:flex;align-items:center;justify-content:center;text-align:center;font:700 8px/1.1 'Open Sans',sans-serif;color:var(--navy)}
  .pockets{position:absolute;left:0;top:515px;width:817px;height:195px}
  .pocket-copy{position:absolute;transform:rotate(180deg);color:#fff;text-align:center;font:400 10px/1.3 'Open Sans',sans-serif}
  .pocket-left-copy{left:45px;top:20px;width:340px}
  .pocket-right-copy{left:440px;top:32px;width:340px}
  .pocket-right-copy b{display:block;margin-top:5px;font:700 12px/1.25 'Open Sans',sans-serif}
</style>
</head>
<body>
<div class="folder">
  <section class="spread">
    <svg class="hero-art" viewBox="0 0 285 285" aria-hidden="false">
      <ellipse cx="140" cy="268" rx="128" ry="13" fill="var(--blue)"/>
      <g role="img" aria-label="Caring hands cradling a photo of a family holding hands on a seaside shore">
        <ellipse cx="140" cy="120" rx="138" ry="118" fill="url(#heroGrad)"/>
      </g>
      <defs>
        <linearGradient id="heroGrad" x1="0" y1="0" x2="0" y2="1">
          <stop offset="0" stop-color="#d592c2"/>
          <stop offset=".35" stop-color="#c9d4e4"/>
          <stop offset=".7" stop-color="#9aa3ae"/>
          <stop offset="1" stop-color="#6478ad"/>
        </linearGradient>
      </defs>
    </svg>

    <p class="intro"><strong>Hereditary cancer screening</strong> provides vital information to help people with a strong personal or family history of cancer understand their own risk of developing the disease. With this information, they can take steps to Potentially Prevent Cancer, Delay the Onset of Cancer or Catch it at an Earlier stage when outcomes and survival rates are Better.</p>

    <p class="motto">Don’t be Afraid of the Answer:<br>Knowledge is Power and Power Eradicates Fear.<br>When You are Fearless, You Will Make all the Right Choices!</p>

    <h1 class="title">HEREDITARY CANCER SCREENING</h1>
    <p class="subtitle">Doctors are the Gatekeepers to Genetic Testing.</p>
    <p class="lead">We have an obligation to help patients understand genetic risk and how testing can guide heath care decisions.</p>

    <svg class="photo-frame" viewBox="0 0 375 240">
      <rect x="20" y="20" width="352" height="190" fill="var(--sky)"/>
      <rect x="10" y="30" width="324" height="205" fill="var(--pink-soft)"/>
      <g role="img" aria-label="Photo of a multi-generation family sharing a meal at an outdoor table">
        <rect x="19" y="38" width="311" height="189" fill="url(#mealGrad)"/>
      </g>
      <g role="img" aria-label="Pink and blue awareness ribbon">
        <rect x="12" y="2" width="38" height="62" rx="8" fill="url(#ribbonGrad)"/>
      </g>
      <defs>
        <linearGradient id="mealGrad" x1="0" y1="0" x2="1" y2="1">
          <stop offset="0" stop-color="#eef1f3"/>
          <stop offset=".5" stop-color="#c8a98f"/>
          <stop offset="1" stop-color="#8d7a6a"/>
        </linearGradient>
        <linearGradient id="ribbonGrad" x1="0" y1="0" x2="1" y2="0">
          <stop offset="0" stop-color="var(--sky)"/>
          <stop offset="1" stop-color="var(--pink)"/>
        </linearGradient>
      </defs>
    </svg>

    <div class="band">
      <div class="brand-seal">Celvara Health Group</div>
      <span class="band-text">THE TEST YOU ORDER FOR YOUR PATIENTS</span>
    </div>
  </section>

  <section class="pockets">
    <svg width="817" height="195" viewBox="0 0 817 195">
      <path d="M2,0 H405 L390,160 Q386,192 360,193 H2 Z" fill="var(--blue-deep)"/>
      <rect x="2" y="0" width="28" height="193" fill="var(--pink-soft)"/>
      <path d="M412,0 L428,160 Q432,192 458,193 H815 V0 Z" fill="var(--blue-deep)"/>
      <rect x="789" y="0" width="26" height="193" fill="var(--pink-soft)"/>
    </svg>
    <p class="pocket-copy pocket-left-copy">There are many benefits to getting tested, regardless of the eventual result. If one of your family members — however distant — had cancer, there is a chance that you inherited a gene mutation that not only increases your personal risk of cancer, but also could be passed to the next generation. Those who are carriers of hereditary cancer gene mutations, could be at risk of getting cancer earlier in life than the general population. The sooner genetic testing is done, the more likely it is that the risk can be managed appropriately.</p>
    <p class="pocket-copy pocket-right-copy">Hereditary cancer screening provides vital information to help people with a strong personal or family history of cancer understand their own risk of developing the disease. With this information, they can take steps to Potentially Prevent Cancer, Delay the Onset of Cancer or Catch it at an Earlier stage when outcomes and survival rates are Better.<b>Identifying an inherited genetic mutation has the potential to prevent cancer and save lives.</b></p>
  </section>
</div>
</body>
</html>
```